Sunscreen Package Design Modern SPF 50

Update current package design to a more modern design target women 16-40 Do not make it playful. Palm Springs is home to movie stars and high income business people PalmSprings is one of the most desired vacation areas in the world. The sun shines 350 days a year. World class Tennis and Golf tournaments are held every year with the worlds top players attending these tournaments

Target Market(s)

Women

Industry/Entity Type

Skin Protection

Font styles to use
Sans Serif

Requirements
Must have
• The words Palm Springs and KORIVELL

```html
<!DOCTYPE html>
<html lang="en">
<head>
<meta charset="utf-8">
<title>Palm Springs KORIVELL Sunscreen – Label Set</title>
<link href="https://fonts.googleapis.com/css2?family=Oswald:wght@500;600&family=Manrope:wght@400;500;600;700&display=swap" rel="stylesheet">
<style>
  :root {
    --stage: #5c5c5c;
    --label-bg: #f8e7da;
    --brown: #7a4f0f;
    --brown-deep: #6b420a;
    --gold-dark: #8a5c17;
    --gold-light: #c9a66b;
    --band: #ecd3b8;
    --body-grey: #8d7f76;
    --white: #ffffff;
  }
  * { margin: 0; padding: 0; box-sizing: border-box; }
  html, body { width: 1200px; height: 614px; overflow: hidden; }
  body {
    background: var(--stage);
    font-family: "Manrope", Arial, sans-serif;
    position: relative;
  }
  .label {
    position: absolute;
    top: 57px;
    width: 278px;
    height: 501px;
    background: var(--label-bg);
    box-shadow: 0 6px 18px rgba(0,0,0,0.25);
    text-align: center;
    color: var(--brown);
    overflow: hidden;
  }
  .label--front { left: 292px; }
  .label--back  { left: 630px; }
  .label > * { position: absolute; left: 0; right: 0; }

  .condensed {
    display: flex;
    justify-content: center;
    white-space: nowrap;
    font-family: "Oswald", "Arial Narrow", sans-serif;
  }

  /* Front */
  .brand-mark {
    top: 31px; left: 81px; right: auto;
    width: 116px; height: 120px;
    border-radius: 50% 50% 45% 45%;
    background: radial-gradient(circle at 50% 30%, var(--gold-light), var(--gold-dark));
  }
  .place-name {
    font-weight: 600;
    font-size: 60px;
    line-height: 54px;
    letter-spacing: -1px;
    color: var(--brown);
    transform: scaleX(0.72);
  }
  .place-name--palm { top: 161px; }
  .place-name--springs { top: 216px; }
  .product-band {
    top: 283px; height: 46px;
    background: linear-gradient(90deg, rgba(236,211,184,0) 0%, var(--band) 18%, var(--band) 82%, rgba(236,211,184,0) 100%);
  }
  .product-name {
    top: 289px;
    font-weight: 600;
    font-size: 29px;
    line-height: 32px;
    letter-spacing: -0.3px;
    color: var(--brown-deep);
    transform: scaleX(0.78);
  }
  .product-name sup { font-size: 11px; line-height: 1; margin: 3px 4px 0 1px; align-self: flex-start; }
  .protection-line {
    top: 339px;
    font-size: 8px; font-weight: 600; letter-spacing: 0.2px;
    white-space: nowrap;
  }
  .spf {
    top: 352px;
    font-weight: 500;
    font-size: 50px; line-height: 50px;
    color: var(--brown);
    transform: scaleX(0.66);
  }
  .benefit-line { font-size: 7.5px; font-weight: 500; color: var(--gold-dark); white-space: nowrap; }
  .benefit-line--lead { top: 410px; }
  .benefit-line--ingredients { top: 426px; }
  .volume-pill {
    top: 450px; left: 97px; right: auto;
    width: 84px; height: 22px; line-height: 22px;
    border-radius: 11px;
    background: var(--white);
    box-shadow: 0 3px 8px rgba(122,79,15,0.12);
    font-size: 7.5px; font-weight: 600; color: var(--brown-deep);
  }

  /* Back */
  .back-heading {
    top: 19px;
    font-weight: 500;
    font-size: 12.5px;
    transform: scaleX(0.67);
    color: var(--brown);
  }
  .back-intro {
    top: 40px; left: 22px; right: 22px;
    font-size: 6.6px; line-height: 14px; color: var(--body-grey);
  }
  .feature-icon {
    left: 122px; right: auto;
    width: 33px; height: 33px; border-radius: 50%;
    background: radial-gradient(circle at 50% 35%, var(--gold-light), var(--gold-dark));
  }
  .feature-icon svg { display: block; width: 33px; height: 33px; }
  .feature-icon--sun { top: 121px; }
  .feature-icon--water { top: 201px; }
  .feature-icon--nourish { top: 278px; }
  .feature-title { font-size: 8px; font-weight: 500; color: var(--brown); white-space: nowrap; }
  .feature-note { font-size: 6.8px; color: var(--body-grey); white-space: nowrap; }
  .feature-title--sun { top: 162px; } .feature-note--sun { top: 176px; }
  .feature-title--water { top: 242px; } .feature-note--water { top: 256px; }
  .feature-title--nourish { top: 320px; } .feature-note--nourish { top: 334px; }
  .divider {
    top: 359px; left: 26px; right: 26px; height: 1px;
    background: linear-gradient(90deg, rgba(201,166,107,0), var(--gold-light), rgba(201,166,107,0));
  }
  .warnings-heading {
    top: 371px;
    font-weight: 500; font-size: 11.5px;
    transform: scaleX(0.75);
  }
  .warnings-text {
    top: 391px;
    font-size: 6.6px; line-height: 12px; color: var(--body-grey);
    white-space: nowrap;
  }
  .warnings-text strong { font-weight: 500; color: #6f625a; }
  .contact {
    top: 470px; left: 40px; right: 40px;
    display: flex; justify-content: space-between;
    font-size: 7px; font-weight: 500; color: var(--brown);
    white-space: nowrap;
  }
</style>
</head>
<body>
  <section class="label label--front">
    <div class="brand-mark" role="img" aria-label="Gold stylised palm tree emblem"></div>
    <div class="condensed place-name place-name--palm">PALM</div>
    <div class="condensed place-name place-name--springs">SPRINGS</div>
    <div class="product-band"></div>
    <div class="condensed product-name">KORIVELL<sup>®</sup>SUNSCREEN</div>
    <div class="protection-line">BROAD SPECTRUM UVA + UVB PROTECTION</div>
    <div class="condensed spf">SPF 50</div>
    <div class="benefit-line benefit-line--lead">Hydrates &amp; Protects with</div>
    <div class="benefit-line benefit-line--ingredients">Hyaluronic Acid • Aloe Vera • Jojoba • Vitamin E</div>
    <div class="volume-pill">3 FL OZ / 88 mL</div>
  </section>

  <section class="label label--back">
    <h2 class="condensed back-heading">DESIGNED FOR LIFE UNDER THE PALM SPRINGS SUN</h2>
    <p class="back-intro">Inspired by one of the world's most iconic luxury destinations, KORIVELL® delivers advanced sun protection with a lightweight feel that disappears into your skin. Whether you're enjoying championship golf, world-class tennis, poolside afternoons, or everyday adventures, KORIVELL keeps your skin protected, hydrated, and radiant.</p>

    <div class="feature-icon feature-icon--sun">
      <svg viewBox="0 0 33 33" fill="none" stroke="#fff" stroke-width="1.4" stroke-linecap="round">
        <circle cx="16.5" cy="16.5" r="4" fill="#fff"/>
        <path d="M16.5 8.5v2M16.5 22.5v2M8.5 16.5h2M22.5 16.5h2M10.8 10.8l1.4 1.4M20.8 20.8l1.4 1.4M10.8 22.2l1.4-1.4M20.8 12.2l1.4-1.4"/>
      </svg>
    </div>
    <div class="feature-title feature-title--sun">Broad Spectrum SPF 50 Protection</div>
    <div class="feature-note feature-note--sun">Protects against UVA/UVB rays</div>

    <div class="feature-icon feature-icon--water">
      <svg viewBox="0 0 33 33" fill="none" stroke="#fff" stroke-width="1.1" stroke-linecap="round">
        <path d="M16.5 10.5c2.5 3.2 3.6 5.2 3.6 6.8a3.6 3.6 0 0 1-7.2 0c0-1.6 1.1-3.6 3.6-6.8z" fill="#fff" stroke="none"/>
        <path d="M9.5 14a7.5 7.5 0 0 1 4-5M23.5 19a7.5 7.5 0 0 1-4 5"/>
      </svg>
    </div>
    <div class="feature-title feature-title--water">Water Resistant</div>
    <div class="feature-note feature-note--water">80 Minutes</div>

    <div class="feature-icon feature-icon--nourish">
      <svg viewBox="0 0 33 33" fill="none" stroke="#fff" stroke-width="1.1" stroke-linecap="round">
        <path d="M17.5 9.5c-4 2-5 5.5-3.5 9 3.5-1 5-4.5 3.5-9z" fill="#fff" stroke="none"/>
        <path d="M14 18.5l2-4"/>
        <path d="M10 21c2 2 11 2 13 0"/>
      </svg>
    </div>
    <div class="feature-title feature-title--nourish">Hydrating &amp; Nourishing</div>
    <div class="feature-note feature-note--nourish">Hyaluronic Acid, Aloe, Jojoba Cucumber &amp; Vitamin E</div>

    <div class="divider"></div>
    <h3 class="condensed warnings-heading">WARNINGS</h3>
    <p class="warnings-text">For external use only. Do not use on damaged or broken skin.<br>Avoid contact with eyes. If contact occurs, rinse thoroughly with water.<br><strong>Keep out of reach of children.</strong></p>

    <div class="contact">
      <span>www.korivell.com</span><span>|</span><span>hello@korivell.com</span>
    </div>
  </section>
</body>
</html>
```